Quill Ride Business Cards

**As soon as there are some quality ideas presented, I will guarantee payment**

We require a template business card with 3 variations based on the following roles:

**Driver Specific version
Communicate;

-More customers, tips, safety, money
-GPS enabled
-no commitment required
-WE PAY YOU (first 3 months)
-Signup here: www.quillride.ca/drivers
-Incorporate QR code - provided
-Customer ratings
-Brokerage independent

**Staff Specific version
Communicate;

-www.quillride.ca
-GPS enabled hailing solution
-Taxis, Limosines, Town Cars
-Name, phone, email

**Customer Specific version
Communicate;
-www.quillride.ca
-Free Service
-Driver ratings
-No busy signals

Logo - provided
Main colours - Black, Yellow
Double sided card
Updates

Thanks for all the submissions, as promised, now that there are some sufficiently creative submissions I have guaranteed this project.  I will be giving some feedback and additional direction today.

Thanks,
Doug

A couple additional requirements;

The "customer" card will require 2 QR codes on it.  1 for iPhone app install and the other for Android app install.

All QR codes need to be at least 3.2cm x 3.2cm

Reason: Reason for extension is that I've gotten busy with another aspect of my business and haven't been able to provide feedback in a timely manner. Hence none of the designs are currently developed to the point that I'm ready to close the contest. PLEASE re-read the design brief to ensure you are addressing the requirements!

Industry/Entity Type

Business

Requirements
Must have
• The full logo on at least one side of the card. Just "QuillRide" text on the other is fine.

QR code integrated into card design

Clean and Simple design with high contrast
Should not have
• cluttered or overly ornate / fancy text

```html
<!DOCTYPE html>
<html lang="en">
<head>
<meta charset="utf-8">
<title>QuillRide Business Card</title>
<link href="https://fonts.googleapis.com/css2?family=PT+Sans:ital,wght@0,400;0,700;1,700&display=swap" rel="stylesheet">
<style>
  :root {
    --page: #e6e4e0;
    --yellow: #f7e91c;
    --gold: #f5c400;
    --ink: #1f1f1f;
    --card-dark: #2a2a2a;
    --card-mid: #3b3b3b;
    --white: #ffffff;
    --checker: #9c8f1a;
  }
  * { margin: 0; padding: 0; box-sizing: border-box; }
  html, body { width: 1200px; height: 900px; overflow: hidden; }
  body {
    background: var(--page);
    font-family: "PT Sans", Arial, sans-serif;
    position: relative;
  }
  .card {
    position: absolute;
    top: 298px;
    width: 535px;
    height: 305px;
    border-radius: 12px;
    overflow: hidden;
    background: var(--card-dark);
    box-shadow: 0 3px 10px rgba(0,0,0,0.25);
  }
  .card--front { left: 62px; }
  .card--back {
    left: 625px;
    background: radial-gradient(ellipse at 50% 50%, var(--card-mid) 0%, var(--card-dark) 55%, #1c1c1c 100%);
  }
  .checker-band {
    position: absolute;
    left: 0; width: 100%; height: 24px;
    background: linear-gradient(180deg, var(--yellow) 0%, var(--checker) 50%, var(--yellow) 100%);
  }
  .checker-band--top { top: 0; }
  .checker-band--bottom { bottom: 0; }
  .tagline-band {
    position: absolute;
    top: 24px; left: 0; width: 100%; height: 80px;
    background: var(--yellow);
  }
  .tagline {
    position: absolute;
    top: 40px; left: 30px;
    color: var(--ink);
    font-weight: 700;
    font-style: italic;
    font-size: 18px;
    line-height: 25px;
  }
  .brand {
    position: absolute;
    display: flex;
    align-items: center;
    gap: 10px;
  }
  .brand__dot {
    width: 26px; height: 26px;
    border-radius: 50%;
    background: var(--gold);
  }
  .brand__name {
    color: var(--gold);
    font-weight: 700;
    font-size: 40px;
    line-height: 1;
  }
  .card--front .brand { left: 290px; top: 118px; }
  .card--back .brand { left: 50%; top: 128px; transform: translateX(-50%); }
  .contact { position: absolute; left: 56px; top: 118px; color: var(--white); }
  .contact__name { color: var(--yellow); font-weight: 700; font-size: 20px; }
  .contact__role { font-size: 13px; margin-top: 4px; }
  .contact__lines { margin-top: 18px; font-size: 14px; line-height: 19px; }
  .contact__line { display: flex; align-items: center; gap: 8px; }
  .contact__line--email { margin-top: 20px; }
  .contact__line svg { width: 13px; height: 13px; flex: none; }
  .website {
    position: absolute;
    top: 252px; left: 0; width: 100%;
    text-align: center;
    color: var(--white);
    font-weight: 700;
    font-style: italic;
    font-size: 13px;
    letter-spacing: 2.5px;
  }
</style>
</head>
<body>
  <section class="card card--front">
    <div class="checker-band checker-band--top" role="img" aria-label="Yellow and black checkered taxi band"></div>
    <div class="tagline-band"></div>
    <p class="tagline">GPS enabled hailing solution<br>Taxis, Limosines, Town Cars</p>
    <div class="contact">
      <p class="contact__name">Nora Feldway</p>
      <p class="contact__role">Admin Staff</p>
      <div class="contact__lines">
        <p class="contact__line">
          <svg viewBox="0 0 14 14" aria-hidden="true"><path fill="#f7e91c" d="M1 4c0-2 2-3 6-3s6 1 6 3l-3 1-1-2H5L4 5zM3 7h8l1 6H2z"/><circle cx="7" cy="9.5" r="1.6" fill="#2a2a2a"/></svg>
          780.555.013
        </p>
        <p class="contact__line">
          <svg viewBox="0 0 14 14" aria-hidden="true"><path fill="#f7e91c" d="M1 4c0-2 2-3 6-3s6 1 6 3l-3 1-1-2H5L4 5zM3 7h8l1 6H2z"/><circle cx="7" cy="9.5" r="1.6" fill="#2a2a2a"/></svg>
          780.555.0195
        </p>
        <p class="contact__line contact__line--email">
          <svg viewBox="0 0 14 14" aria-hidden="true"><rect x="1" y="3" width="12" height="8" fill="none" stroke="#f7e91c" stroke-width="1.4"/><path d="M1 3l6 5 6-5" fill="none" stroke="#f7e91c" stroke-width="1.4"/></svg>
          nfeldway@quillride.ca
        </p>
      </div>
    </div>
    <div class="brand">
      <span class="brand__dot"></span>
      <span class="brand__name">QuillRide</span>
    </div>
    <div class="checker-band checker-band--bottom" role="img" aria-label="Yellow and black checkered taxi band"></div>
  </section>

  <section class="card card--back">
    <div class="checker-band checker-band--top" role="img" aria-label="Yellow and black checkered taxi band"></div>
    <div class="brand">
      <span class="brand__dot"></span>
      <span class="brand__name">QuillRide</span>
    </div>
    <p class="website">www.quillride.ca</p>
    <div class="checker-band checker-band--bottom" role="img" aria-label="Yellow and black checkered taxi band"></div>
  </section>
</body>
</html>
```